New Business Card Design Project

We would like a business card that represents the sale of boat, home, auto, and life insurance.

The logo can change colors to meet the look of the design if needed.

Industry/Entity Type

Business

```html
<!DOCTYPE html>
<html lang="en">
<head>
<meta charset="utf-8">
<title>Northwind Financial – Business Card</title>
<link href="https://fonts.googleapis.com/css2?family=Josefin+Sans:wght@400&family=Open+Sans:wght@400;600&display=swap" rel="stylesheet">
<style>
  :root {
    --backdrop: #d9dadb;
    --teal: #3c7a8d;
    --white: #ffffff;
    --ink: #3a3a3a;
    --strip: #3d3d3f;
    --photo-a: #7a3b2c;
    --photo-b: #c99a7e;
  }
  * { box-sizing: border-box; margin: 0; padding: 0; }
  html, body {
    width: 1200px; height: 676px; overflow: hidden;
    background: var(--backdrop);
  }
  .stage {
    position: relative; width: 1200px; height: 676px;
    display: flex; align-items: center; justify-content: center; gap: 40px;
  }
  .card {
    position: relative; width: 540px; height: 310px;
    box-shadow: 0 6px 18px rgba(0,0,0,.18);
    overflow: hidden;
    background: var(--teal);
  }

  /* Brand lockup (shared) */
  .brand {
    position: absolute; left: 0; right: 0;
    display: flex; flex-direction: column; align-items: center;
    text-align: center; white-space: nowrap;
  }
  .brand-mark { border-radius: 50%; background: currentColor; }
  .brand-name {
    font-family: "Josefin Sans", sans-serif; font-weight: 400;
    text-transform: uppercase;
  }
  .brand-sub {
    font-family: "Josefin Sans", sans-serif; font-weight: 400;
    text-transform: uppercase;
  }
  .tagline { font-family: "Open Sans", sans-serif; }

  /* Front */
  .front-brand { top: 92px; color: var(--white); }
  .front-brand .brand-mark { width: 22px; height: 22px; margin-bottom: 12px; }
  .front-brand .brand-name { font-size: 34px; letter-spacing: 8px; line-height: 1; }
  .front-brand .brand-sub { font-size: 18px; letter-spacing: 7px; margin-top: 6px; }
  .front-brand .tagline { font-size: 15px; letter-spacing: 1.5px; margin-top: 8px; }

  /* Back */
  .back-panel {
    position: absolute; left: 0; top: 0; bottom: 0; width: 225px;
    background: var(--white);
  }
  .back-brand { top: 30px; color: var(--ink); }
  .back-brand .brand-mark { width: 12px; height: 12px; margin-bottom: 8px; background: var(--teal); }
  .back-brand .brand-name { font-size: 17px; letter-spacing: 4px; line-height: 1; }
  .back-brand .brand-sub { font-size: 11px; letter-spacing: 4px; margin-top: 4px; color: var(--teal); }
  .back-brand .tagline { font-size: 10px; letter-spacing: .6px; margin-top: 4px; }
  .portrait {
    position: absolute; left: 55px; top: 128px; width: 112px; height: 124px;
    border: 2px solid var(--teal); padding: 3px; background: var(--white);
  }
  .portrait-fill {
    width: 100%; height: 100%;
    background: linear-gradient(160deg, var(--photo-b), var(--photo-a));
  }
  .icon-strip {
    position: absolute; left: 225px; top: 140px; bottom: 0; width: 24px;
    background: var(--strip);
    display: flex; flex-direction: column; align-items: center;
    padding-top: 10px; gap: 12px;
  }
  .icon-strip svg { width: 11px; height: 11px; fill: none; stroke: var(--white); stroke-width: 1.6; }
  .person {
    position: absolute; left: 262px; top: 92px; color: var(--white);
    font-family: "Open Sans", sans-serif;
  }
  .person-name { font-size: 22px; font-weight: 400; }
  .person-role { font-size: 12px; margin-top: 2px; }
  .contact {
    position: absolute; left: 262px; top: 172px; color: var(--white);
    font-family: "Open Sans", sans-serif; font-size: 13px; line-height: 17px;
    list-style: none; white-space: nowrap;
  }
  .contact .web { margin-top: 4px; }
</style>
</head>
<body>
<main class="stage">
  <section class="card card-front" aria-label="Card front">
    <div class="brand front-brand">
      <span class="brand-mark"></span>
      <div class="brand-name">Northwind</div>
      <div class="brand-sub">Financial</div>
      <div class="tagline">investments &amp; insurance</div>
    </div>
  </section>

  <section class="card card-back" aria-label="Card back">
    <div class="back-panel">
      <div class="brand back-brand">
        <span class="brand-mark"></span>
        <div class="brand-name">Northwind</div>
        <div class="brand-sub">Financial</div>
        <div class="tagline">investments &amp; insurance</div>
      </div>
      <div class="portrait">
        <div class="portrait-fill" role="img" aria-label="Portrait photo of the agent"></div>
      </div>
    </div>

    <div class="icon-strip" aria-hidden="true">
      <svg viewBox="0 0 12 12"><path d="M6 11 C3 7 2.5 5.5 2.5 4.5 a3.5 3.5 0 0 1 7 0 C9.5 5.5 9 7 6 11z"/><circle cx="6" cy="4.5" r="1.2"/></svg>
      <svg viewBox="0 0 12 12"><rect x="3" y="1" width="6" height="10" rx="1"/><line x1="5" y1="9" x2="7" y2="9"/></svg>
      <svg viewBox="0 0 12 12"><rect x="2" y="2" width="8" height="8"/></svg>
      <svg viewBox="0 0 12 12"><rect x="1" y="3" width="10" height="7"/><path d="M1 3 L6 7 L11 3"/></svg>
      <svg viewBox="0 0 12 12"><circle cx="6" cy="6" r="4.5"/><ellipse cx="6" cy="6" rx="2" ry="4.5"/><line x1="1.5" y1="6" x2="10.5" y2="6"/></svg>
    </div>

    <div class="person">
      <div class="person-name">your name</div>
      <div class="person-role">designation</div>
    </div>

    <ul class="contact">
      <li>address (street address</li>
      <li>suite number, city, state, zip</li>
      <li>0123 456 789</li>
      <li>0123 456 789</li>
      <li>youremail@mail.com</li>
      <li class="web">www.yourwebsite.com</li>
    </ul>
  </section>
</main>
</body>
</html>
```